Telecommunications/Power civil contractor needs business card design

Were a new telecommunications/power underground civil contractor that is looking for a new business card design. Our company colours are silver or grey and orange. Feel free to use the white background logo or the black background logo.

Target Market(s)

Local contractors, utility companies, private sector mining/energy companies, developers.

Industry/Entity Type

Telecommunications

Contact Information for Business Card

Each card will need the following info:
Persons name:
Title:
E-mail:
Phone number:
Shop Address:
Mailing Address:

Requirements
Must have
• Each card will need the following info:
• Persons name:
• Title:
• E-mail:
• Phone number:
• Shop Address:
• Mailing Address:

```html
<!DOCTYPE html>
<html lang="en">
<head>
<meta charset="utf-8">
<title>Ridgeway Contracting Inc — Business Card</title>
<link rel="stylesheet" href="https://fonts.googleapis.com/css2?family=Roboto:wght@400;500;700;900&display=swap">
<style>
  :root {
    --orange: #f0541e;
    --grey-dark: #4d4d4d;
    --grey-mid: #8a8a8a;
    --grey-light: #b9b9b9;
    --card-white: #ffffff;
    --back-top: #6e6e6e;
    --back-bottom: #4a4a4a;
    --backdrop: #e6e6e6;
    --back-mark: #d9d9d9;
  }
  * { box-sizing: border-box; margin: 0; padding: 0; }
  html, body {
    width: 1200px; height: 950px; overflow: hidden;
    background: var(--backdrop);
    font-family: "Roboto", Arial, sans-serif;
  }
  .sheet { position: relative; width: 1200px; height: 950px; }

  .card {
    position: absolute; left: 250px; width: 700px; height: 400px;
    overflow: hidden;
    box-shadow: 0 6px 18px rgba(0,0,0,0.18);
  }

  /* Back face */
  .card-back {
    top: 45px;
    background: linear-gradient(160deg, var(--back-top), var(--back-bottom));
    display: flex; flex-direction: column; align-items: center; justify-content: center;
    gap: 18px;
  }
  .card-back .mark-circle {
    width: 120px; height: 120px; border-radius: 50%;
    border: 8px solid var(--back-mark);
  }
  .card-back .brand-name {
    color: var(--back-mark); font-weight: 900; font-size: 40px;
    letter-spacing: 1px; text-transform: uppercase; text-align: center; line-height: 1.05;
  }
  .card-back .brand-name small { display: block; font-size: 20px; letter-spacing: 3px; font-weight: 900; }

  /* Front face */
  .card-front { top: 505px; background: var(--card-white); }
  .top-band { position: absolute; left: 0; top: 0; width: 100%; height: 14px; background: var(--orange); }
  .bottom-bands { position: absolute; left: 0; bottom: 0; width: 100%; height: 28px; }
  .bottom-bands .band { position: absolute; bottom: 0; }
  .band-left { left: 0; width: 38%; height: 14px; background: var(--grey-mid); }
  .band-centre { left: 38%; width: 37%; height: 28px; background: var(--orange); }
  .band-right { left: 75%; width: 25%; height: 14px; background: var(--grey-mid); }

  .brand {
    position: absolute; left: 40px; top: 80px; width: 300px;
    display: flex; flex-direction: column; align-items: center; gap: 14px;
  }
  .brand .mark-circle {
    width: 96px; height: 96px; border-radius: 50%;
    border: 7px solid var(--orange);
  }
  .brand .brand-name {
    color: var(--orange); font-weight: 900; font-size: 34px;
    text-transform: uppercase; text-align: center; line-height: 1.05; letter-spacing: 0.5px;
  }
  .brand .brand-name small { display: block; font-size: 17px; letter-spacing: 2.5px; }

  .divider {
    position: absolute; left: 370px; top: 46px; width: 1px; height: 280px;
    background: var(--grey-light);
  }

  .contact { position: absolute; left: 400px; top: 44px; width: 290px; color: var(--grey-dark); }
  .person-name { color: var(--orange); font-weight: 700; font-size: 26px; line-height: 1.2; }
  .person-title { font-size: 16px; margin-top: 1px; }
  .addresses { display: flex; flex-direction: column; gap: 8px; margin-top: 14px; }
  .address { font-size: 16px; line-height: 1.3; }
  .address-label { font-weight: 700; }
  .contact-list { list-style: none; margin-top: 12px; font-size: 16px; }
  .contact-list li { display: flex; align-items: center; gap: 12px; height: 26px; }
  .contact-list svg { width: 16px; height: 16px; flex: none; }
</style>
</head>
<body>
<main class="sheet">

  <section class="card card-back" aria-label="Business card, back">
    <div class="mark-circle"></div>
    <p class="brand-name">Ridgeway<small>Contracting Inc</small></p>
  </section>

  <section class="card card-front" aria-label="Business card, front">
    <div class="top-band"></div>

    <div class="brand">
      <div class="mark-circle"></div>
      <p class="brand-name">Ridgeway<small>Contracting Inc</small></p>
    </div>

    <div class="divider"></div>

    <div class="contact">
      <p class="person-name">Mara Lindqvist</p>
      <p class="person-title">President</p>
      <div class="addresses">
        <p class="address"><span class="address-label">Shop:</span> 2710 Harrow Lane<br>Elm Ridge, NY 11420</p>
        <p class="address"><span class="address-label">Mail:</span> PO Box 318<br>Elm Ridge, NY 11421</p>
      </div>
      <ul class="contact-list">
        <li>
          <svg viewBox="0 0 16 16" aria-hidden="true"><path fill="#f0541e" d="M3.5 1.5l2.5 0 1 3.5-1.7 1.2a8 8 0 0 0 4.5 4.5l1.2-1.7 3.5 1v2.5c0 .8-.7 1.5-1.5 1.5A12 12 0 0 1 2 3c0-.8.7-1.5 1.5-1.5z"/></svg>
          555 0142 7781
        </li>
        <li>
          <svg viewBox="0 0 16 16" aria-hidden="true"><rect x="1" y="3" width="14" height="10" rx="1" fill="#f0541e"/><path d="M1.5 3.8L8 9l6.5-5.2" fill="none" stroke="#fff" stroke-width="1.3"/></svg>
          mara@ridgewaycivil.com
        </li>
        <li>
          <svg viewBox="0 0 16 16" aria-hidden="true"><circle cx="8" cy="8" r="7" fill="#f0541e"/><path d="M1 8h14M8 1c-3 3.5-3 10.5 0 14M8 1c3 3.5 3 10.5 0 14" fill="none" stroke="#fff" stroke-width="1"/></svg>
          www.ridgewaycivil.com
        </li>
      </ul>
    </div>

    <div class="bottom-bands">
      <span class="band band-left"></span>
      <span class="band band-centre"></span>
      <span class="band band-right"></span>
    </div>
  </section>

</main>
</body>
</html>
```